full stationary design for a modern sleek design company

we are a design company that does modern minimalistic interior design works as well as other design services for high end clients.
we need a full stationary design including and not limited to (double sided business card, letter head, envelopes, documents folder...etc) that reflects the modern style design we do.
sleek modern and minimalistic is the requirements.
Updates

please use the latest attached files as there was a slight modification on the logo Added Wednesday, March 1, 2017

minor update on the logo files in JPG and PSD has been updated kindly follow the new attachments. Added Thursday, March 2, 2017

Target Market(s)

modern minimalist clients

Industry/Entity Type

Design Agency

Requirements
Must have
• the logo
Nice to have
• i like the colors in the colored 3D logo attached
Should not have
• too many colors

```html
<!DOCTYPE html>
<html lang="en">
<head>
<meta charset="utf-8">
<title>Linea Atelier – Business Card</title>
<link rel="stylesheet" href="https://fonts.googleapis.com/css2?family=Source+Sans+3:wght@400;600&family=Michroma&display=swap">
<style>
  :root {
    --page-bg: #d9d6d2;
    --card-bg: #f4f3f1;
    --ink: #2a2a2c;
    --accent: #e8742a;
    --accent-light: #f29a52;
    --accent-deep: #d95a14;
    --photo-tone: #8c9097;
    --on-accent: #ffffff;
    --on-accent-soft: #fde7d6;
  }
  * { box-sizing: border-box; margin: 0; padding: 0; }
  html, body {
    width: 1200px; height: 969px; overflow: hidden;
    background: var(--page-bg);
    font-family: "Source Sans 3", "Myriad Pro", Arial, sans-serif;
  }
  .card {
    position: absolute; left: 100px; top: 200px;
    width: 1000px; height: 570px;
    background: var(--card-bg);
    border-radius: 64px 6px 6px 6px;
    overflow: hidden;
    box-shadow: 0 10px 30px rgba(0,0,0,.18);
  }
  .card-art { position: absolute; inset: 0; }
  .brand {
    position: absolute; left: 520px; top: 92px;
    display: flex; align-items: center; gap: 18px;
  }
  .brand-square { width: 58px; height: 58px; background: var(--accent); }
  .brand-name {
    font-family: "Michroma", "Source Sans 3", sans-serif;
    font-size: 34px; color: var(--ink); letter-spacing: 1px; line-height: 1;
  }
  .brand-tagline {
    font-family: "Michroma", "Source Sans 3", sans-serif;
    font-size: 19px; color: var(--accent); letter-spacing: 6px;
    margin-top: 8px; line-height: 1;
  }
  .person { position: absolute; left: 46px; top: 322px; color: var(--on-accent); }
  .person-name { font-size: 33px; font-weight: 600; letter-spacing: .5px; line-height: 1.1; }
  .person-title { font-size: 25px; color: var(--on-accent-soft); line-height: 1.2; }
  .contact-list { position: absolute; left: 46px; top: 426px; list-style: none; }
  .contact-list li {
    display: flex; align-items: center; gap: 14px;
    font-size: 25px; color: var(--on-accent-soft); height: 39px;
  }
  .contact-list svg { width: 22px; height: 22px; fill: var(--on-accent-soft); }
  .address {
    position: absolute; right: 60px; top: 426px;
    text-align: right; font-size: 25px; color: var(--on-accent-soft); line-height: 39px;
  }
</style>
</head>
<body>
  <div class="card">
    <svg class="card-art" viewBox="0 0 1000 570" width="1000" height="570" aria-hidden="true">
      <defs>
        <linearGradient id="photoFade" x1="0" x2="1" y1="0" y2="0">
          <stop offset="0" stop-color="#8c9097"/>
          <stop offset=".6" stop-color="#b7b9bc"/>
          <stop offset="1" stop-color="#f4f3f1" stop-opacity="0"/>
        </linearGradient>
        <linearGradient id="bandFill" x1="0" x2="0" y1="0" y2="1">
          <stop offset="0" stop-color="#f29a52"/>
          <stop offset=".45" stop-color="#e8742a"/>
          <stop offset="1" stop-color="#d95a14"/>
        </linearGradient>
      </defs>
      <path d="M0 290 H400 C425 290 430 318 458 318 H1000 V570 H0 Z" fill="url(#bandFill)"/>
      <path d="M0 282 H398" stroke="#9a9a9a" stroke-width="2" fill="none"/>
      <path d="M392 283 C424 283 432 308 462 308 H1000" stroke="#1d1d1f" stroke-width="7" fill="none"/>
    </svg>
    <div role="img" aria-label="Photo of a modern minimalist office interior with meeting table and chairs"
         style="position:absolute;left:0;top:0;width:460px;height:280px;background:linear-gradient(90deg,#8c9097 0%,#b7b9bc 60%,rgba(244,243,241,0) 100%);"></div>

    <div class="brand">
      <span class="brand-square"></span>
      <div>
        <div class="brand-name">LINEA ATELIER</div>
        <div class="brand-tagline">BY MARC DEVAUX</div>
      </div>
    </div>

    <div class="person">
      <div class="person-name">ADAM ROWE</div>
      <div class="person-title">CEO&amp;Founder</div>
    </div>

    <ul class="contact-list">
      <li><svg viewBox="0 0 24 24"><path d="M6.6 10.8a15 15 0 0 0 6.6 6.6l2.2-2.2c.3-.3.7-.4 1-.2 1.1.4 2.3.6 3.6.6.6 0 1 .4 1 1V20c0 .6-.4 1-1 1C10.6 21 3 13.4 3 4c0-.6.4-1 1-1h3.5c.6 0 1 .4 1 1 0 1.3.2 2.5.6 3.6.1.3 0 .7-.2 1z"/></svg>(555) 201 4830</li>
      <li><svg viewBox="0 0 24 24"><path d="M8 1h8a2 2 0 0 1 2 2v18a2 2 0 0 1-2 2H8a2 2 0 0 1-2-2V3a2 2 0 0 1 2-2zm0 3v14h8V4zm4 15.5a1 1 0 1 0 0 2 1 1 0 0 0 0-2z"/></svg>(555) 731 2209</li>
      <li><svg viewBox="0 0 24 24"><path d="M2 5h20v14H2zm2 2v.5l8 5 8-5V7zm0 2.8V17h16V9.8l-8 5z"/></svg>adam@lineaatelier.com</li>
    </ul>

    <div class="address">
      <div>214 Alder Row</div>
      <div>Harbor City, Westland 20415</div>
      <div>www.lineaatelier.com</div>
    </div>
  </div>
</body>
</html>
```